Step and Repeat Backdrop for wedding reception photo booth

Would like to have a Step and Repeat Backdrop (8 foot high by 10 foot wide) that incorporates the wedding logo (attached) and the names Helen and Gavin. Background should be white, and wedding colors are burgundy and gold. Show me creativity :-) I have included some random samples.

```html
<!DOCTYPE html>
<html lang="en">
<head>
<meta charset="utf-8">
<title>Helen &amp; Gavin – Step and Repeat Backdrop</title>
<link rel="stylesheet" href="https://fonts.googleapis.com/css2?family=Pinyon+Script&display=swap">
<style>
  :root {
    --backdrop-white: #ffffff;
    --wedding-gold: #b07d1f;
  }
  html, body {
    margin: 0;
    padding: 0;
    width: 1200px;
    height: 960px;
    overflow: hidden;
    background: var(--backdrop-white);
  }
  .backdrop {
    position: relative;
    width: 1200px;
    height: 960px;
    background: var(--backdrop-white);
  }
  .couple-name {
    position: absolute;
    transform: translate(-50%, -50%);
    margin: 0;
    font-family: "Pinyon Script", cursive;
    font-weight: 400;
    color: var(--wedding-gold);
    white-space: nowrap;
    line-height: 1;
  }
  .couple-name--repeat {
    font-size: 28px;
  }
  .couple-name--feature {
    font-size: 92px;
  }
</style>
</head>
<body>
<main class="backdrop">
  <h1 class="couple-name couple-name--feature" style="left:597px; top:330px;">Helen &amp; Gavin</h1>

  <!-- row 1 -->
  <p class="couple-name couple-name--repeat" style="left:95px; top:92px;">Helen &amp; Gavin</p>
  <p class="couple-name couple-name--repeat" style="left:346px; top:92px;">Helen &amp; Gavin</p>
  <p class="couple-name couple-name--repeat" style="left:597px; top:92px;">Helen &amp; Gavin</p>
  <p class="couple-name couple-name--repeat" style="left:848px; top:92px;">Helen &amp; Gavin</p>
  <p class="couple-name couple-name--repeat" style="left:1097px; top:92px;">Helen &amp; Gavin</p>

  <!-- side columns -->
  <p class="couple-name couple-name--repeat" style="left:206px; top:184px;">Helen &amp; Gavin</p>
  <p class="couple-name couple-name--repeat" style="left:988px; top:184px;">Helen &amp; Gavin</p>
  <p class="couple-name couple-name--repeat" style="left:95px; top:279px;">Helen &amp; Gavin</p>
  <p class="couple-name couple-name--repeat" style="left:1097px; top:279px;">Helen &amp; Gavin</p>
  <p class="couple-name couple-name--repeat" style="left:206px; top:374px;">Helen &amp; Gavin</p>
  <p class="couple-name couple-name--repeat" style="left:988px; top:374px;">Helen &amp; Gavin</p>
  <p class="couple-name couple-name--repeat" style="left:95px; top:474px;">Helen &amp; Gavin</p>
  <p class="couple-name couple-name--repeat" style="left:1097px; top:474px;">Helen &amp; Gavin</p>

  <!-- row 6 -->
  <p class="couple-name couple-name--repeat" style="left:206px; top:566px;">Helen &amp; Gavin</p>
  <p class="couple-name couple-name--repeat" style="left:488px; top:566px;">Helen &amp; Gavin</p>
  <p class="couple-name couple-name--repeat" style="left:706px; top:566px;">Helen &amp; Gavin</p>
  <p class="couple-name couple-name--repeat" style="left:988px; top:566px;">Helen &amp; Gavin</p>

  <!-- row 7 -->
  <p class="couple-name couple-name--repeat" style="left:98px; top:675px;">Helen &amp; Gavin</p>
  <p class="couple-name couple-name--repeat" style="left:349px; top:675px;">Helen &amp; Gavin</p>
  <p class="couple-name couple-name--repeat" style="left:597px; top:675px;">Helen &amp; Gavin</p>
  <p class="couple-name couple-name--repeat" style="left:848px; top:675px;">Helen &amp; Gavin</p>
  <p class="couple-name couple-name--repeat" style="left:1099px; top:675px;">Helen &amp; Gavin</p>

  <!-- row 8 -->
  <p class="couple-name couple-name--repeat" style="left:206px; top:770px;">Helen &amp; Gavin</p>
  <p class="couple-name couple-name--repeat" style="left:491px; top:770px;">Helen &amp; Gavin</p>
  <p class="couple-name couple-name--repeat" style="left:706px; top:770px;">Helen &amp; Gavin</p>
  <p class="couple-name couple-name--repeat" style="left:990px; top:770px;">Helen &amp; Gavin</p>

  <!-- row 9 -->
  <p class="couple-name couple-name--repeat" style="left:100px; top:865px;">Helen &amp; Gavin</p>
  <p class="couple-name couple-name--repeat" style="left:352px; top:865px;">Helen &amp; Gavin</p>
  <p class="couple-name couple-name--repeat" style="left:600px; top:865px;">Helen &amp; Gavin</p>
  <p class="couple-name couple-name--repeat" style="left:851px; top:865px;">Helen &amp; Gavin</p>
  <p class="couple-name couple-name--repeat" style="left:1102px; top:865px;">Helen &amp; Gavin</p>
</main>
</body>
</html>
```